Website for enterprise software start-up

We need a new Wordpress website. We are an early stage start-up focused on mobile video technology for cellular operators. The audience is strategy, marketing and customer acquisition execs from the operators.

The purpose of the site is to act as a sales brochure and capture leads. A demo app can be downloaded from the current site, want to put that behind a contact form.

Current website is at www.velmora.tv. Similar number of pages. Looking for a clean design template, with minimal customization. Blog will remain as is.

Want to be able to modify the copy via Wordpress. Reference designs I like: quandrix.com, briskfold7metrics.com

Target Market(s)

Mobile operators and MVNOs in the US and Asia Pacific regions

Industry/Entity Type

Business Software

Coding

Coded - Design and coding required

Number of Pages Required

4 page

Font styles to use
Sans Serif

Colors
f78f20

Requirements
Must have
• Form for downloading sample apps.
• Landing page with image, Product, Blog, About, Contact
• Team page

```html
<!DOCTYPE html>
<html lang="en">
<head>
<meta charset="utf-8">
<title>Velmora Media</title>
<link href="https://fonts.googleapis.com/css2?family=Questrial&family=Lato:wght@400;700&display=swap" rel="stylesheet">
<style>
:root{
  --orange:#e0731a;
  --orange-bright:#f78f20;
  --ink:#2b2b2b;
  --body:#555;
  --muted:#888;
  --grey-band:#f2f2f2;
  --strip:#ececec;
  --dark:#333536;
  --footer:#1f2226;
  --white:#fff;
  --field:#fff;
}
*{box-sizing:border-box;margin:0;padding:0}
html,body{width:1200px;height:3377px;overflow:hidden}
body{position:relative;font-family:"Lato",sans-serif;color:var(--body);background:var(--white)}
.abs{position:absolute}
h2,.heading{font-family:"Questrial",sans-serif}

/* header */
.site-header{left:0;top:0;width:1200px;height:82px;background:var(--white)}
.brand{left:80px;top:8px;display:flex;align-items:center;gap:10px}
.brand-square{width:50px;height:60px;background:var(--orange)}
.brand-name{font-family:"Questrial",sans-serif;font-size:44px;color:var(--ink);font-weight:400;letter-spacing:-0.5px}
.main-nav{left:488px;top:36px;display:flex;gap:0}
.main-nav a{font-family:"Questrial",sans-serif;font-size:15px;color:var(--ink);text-decoration:none;margin-right:56px;position:relative;letter-spacing:.3px}
.main-nav a:last-child{margin-right:0}
.main-nav a.active{color:var(--orange)}
.main-nav a.active::after{content:"";position:absolute;left:50%;top:24px;margin-left:-7px;border:7px solid transparent;border-top:9px solid var(--orange)}

/* hero */
.hero{left:0;top:82px;width:1200px;height:558px;background:linear-gradient(100deg,#5a5553 0%,#7a716c 30%,#6d6866 55%,#4c4d50 100%)}
.hero-shade{left:0;top:0;width:1200px;height:558px;background:rgba(30,30,30,.35)}
.hero-title{left:0;top:155px;width:1200px;text-align:center;color:var(--white);font-family:"Questrial",sans-serif;font-size:39px;font-weight:700;letter-spacing:.3px}
.hero-sub{left:0;top:233px;width:1200px;text-align:center;color:var(--white);font-size:21px;line-height:32px}
.btn{display:inline-block;background:var(--orange);color:var(--white);font-family:"Questrial",sans-serif;text-align:center}
.hero-btn{left:478px;top:329px;width:244px;height:56px;line-height:56px;font-size:24px}
.hero-dots{left:567px;top:406px;display:flex;gap:5px}
.hero-dots span{width:12px;height:12px;border-radius:50%;background:var(--white)}
.hero-dots span.current{background:transparent;border:2px solid var(--white)}

/* about */
.section-title{left:0;width:1200px;text-align:center;font-size:35px;color:var(--ink)}
.section-title::after{content:"";display:block;width:60px;height:2px;background:#bbb;margin:14px auto 0}
.about-list{width:480px;list-style:none}
.about-list li{position:relative;padding-left:38px;font-size:16.5px;line-height:26px;color:var(--body)}
.about-list svg{position:absolute;left:0;top:2px}
.btn-view{left:530px;top:1535px;width:138px;height:52px;line-height:52px;font-size:24px}

/* team */
.team{left:0;top:1632px;width:1200px;height:578px;background:var(--grey-band)}
.quote{width:480px;padding:24px 28px;color:var(--white);font-weight:700;font-size:16.5px;line-height:28px;border-radius:8px}
.quote.dark{background:#363636}
.quote.orange{background:var(--orange)}
.quote::after{content:"";position:absolute;left:130px;bottom:-28px;border-left:0 solid transparent;border-right:40px solid transparent;border-top:30px solid}
.quote.dark::after{border-top-color:#363636}
.quote.orange::after{border-top-color:var(--orange);left:140px}
.portrait{width:160px;height:112px}
.member-name{font-family:"Questrial",sans-serif;font-size:27px;font-weight:700;color:var(--ink)}
.member-role{font-size:16px;color:var(--muted);margin-top:10px}
.slider-arrow{width:38px;height:38px;border-radius:50%;background:var(--white);border:1px solid #ddd;display:flex;align-items:center;justify-content:center}

/* clients */
.client-box{top:2355px;height:116px;border:3px solid #e6e6e6;background:var(--white);display:flex;align-items:center;justify-content:center;gap:10px;font-size:22px;font-weight:700;color:#8a8a8a}
.client-box i{width:14px;height:14px;background:#9a9a9a;display:block}
.client-arrow{top:2390px}

/* partner strip */
.partner{left:0;top:2525px;width:1200px;height:92px;background:var(--strip)}
.partner-badge{left:160px;top:20px;width:156px;height:56px;border-radius:8px;background:#d9dde3}
.partner-text{left:344px;top:34px;font-size:20px;color:var(--ink)}
.partner-text strong{color:var(--orange)}

/* download */
.download{left:0;top:2617px;width:1200px;height:231px;background:linear-gradient(90deg,#4b5866 0%,#7d8791 45%,#56606b 100%)}
.download-title{left:0;top:36px;width:1200px;text-align:center;color:var(--white);font-family:"Questrial",sans-serif;font-size:28px}
.store-btn{top:93px;width:158px;height:52px;background:#1d1d1d;border:1px solid #888;border-radius:5px;color:var(--white);display:flex;flex-direction:column;justify-content:center;padding-left:48px;font-size:10px;line-height:12px}
.store-btn b{font-size:16px;font-weight:700;line-height:20px}
.store-btn span.mark{position:absolute;left:14px;top:14px;width:22px;height:22px;border-radius:50%;background:#666}

/* contact form */
.contact{left:0;top:2848px;width:1200px;height:469px;background:var(--dark)}
.mail-badge{left:552px;top:-38px;width:96px;height:96px;border-radius:50%;background:var(--orange);border:4px solid var(--white);display:flex;align-items:center;justify-content:center}
.field{background:var(--field);font-size:15px;font-style:italic;color:#666;padding:0 18px;display:flex;align-items:center}
.field.message{align-items:flex-start;padding-top:18px}
.btn-submit{left:102px;top:402px;width:120px;height:42px;line-height:42px;font-family:"Lato",sans-serif;font-weight:700;font-size:19px}

/* footer */
.site-footer{left:0;top:3317px;width:1200px;height:60px;background:var(--footer)}
.copyright{left:80px;top:22px;font-size:11px;color:#ccc}
.social{left:984px;top:17px;display:flex;gap:8px}
.social span{width:24px;height:24px;border-radius:50%;background:#4a6fa5;display:block}
</style>
</head>
<body>

<header class="site-header abs">
  <div class="brand abs">
    <span class="brand-square"></span>
    <span class="brand-name">velmora media</span>
  </div>
  <nav class="main-nav abs">
    <a class="active" href="#">HOME</a>
    <a href="#">PRODUCT</a>
    <a href="#">BLOG</a>
    <a href="#">ABOUT US</a>
    <a href="#">OUR TEAM</a>
    <a href="#">CONTACT US</a>
  </nav>
</header>

<section class="hero abs" role="img" aria-label="Photo of a woman watching video on her smartphone">
  <div class="hero-shade abs"></div>
  <h1 class="hero-title abs">High Quality Mobile Engagement</h1>
  <p class="hero-sub abs">We Engage Mobile Audiences With The Right Video Content At<br>The Perfect Moment</p>
  <a class="btn hero-btn abs">Get Sample Apps</a>
  <div class="hero-dots abs"><span class="current"></span><span></span><span></span><span></span></div>
</section>

<section class="about">
  <h2 class="section-title abs" style="top:680px">About Us</h2>
  <ul class="about-list abs" style="left:84px;top:790px">
    <li style="height:130px"><svg width="22" height="22" viewBox="0 0 22 22"><rect x="1" y="4" width="16" height="16" fill="none" stroke="#e0731a" stroke-width="2.4"/><path d="M5 11l4 4 11-12" fill="none" stroke="#e0731a" stroke-width="3"/></svg>Other signals include headphones in, in motion from the accelerometer, whether user has coverage or not.</li>
    <li style="height:130px"><svg width="22" height="22" viewBox="0 0 22 22"><rect x="1" y="4" width="16" height="16" fill="none" stroke="#e0731a" stroke-width="2.4"/><path d="M5 11l4 4 11-12" fill="none" stroke="#e0731a" stroke-width="3"/></svg>Velmora Media is a content platform for operators, that allows them to create new business models based on mobile video.</li>
    <li style="height:130px"><svg width="22" height="22" viewBox="0 0 22 22"><rect x="1" y="4" width="16" height="16" fill="none" stroke="#e0731a" stroke-width="2.4"/><path d="M5 11l4 4 11-12" fill="none" stroke="#e0731a" stroke-width="3"/></svg>Velmora's platforms predictively pre-positions video content, and uses ML to reveal video at the perfect moment for maximum engagement.</li>
    <li style="height:130px"><svg width="22" height="22" viewBox="0 0 22 22"><rect x="1" y="4" width="16" height="16" fill="none" stroke="#e0731a" stroke-width="2.4"/><path d="M5 11l4 4 11-12" fill="none" stroke="#e0731a" stroke-width="3"/></svg>One of the common solutions is a “value exchange”, where the consumers receive data or dollars off their bill, in exchange for viewing promotional content</li>
    <li><svg width="22" height="22" viewBox="0 0 22 22"><rect x="1" y="4" width="16" height="16" fill="none" stroke="#e0731a" stroke-width="2.4"/><path d="M5 11l4 4 11-12" fill="none" stroke="#e0731a" stroke-width="3"/></svg>The type of content we see as most effective is native vertical video. Think of Flicker 3V ads, but published directly to the phone, rather than a specific app</li>
  </ul>
  <ul class="about-list abs" style="left:638px;top:790px">
    <li style="height:130px"><svg width="22" height="22" viewBox="0 0 22 22"><rect x="1" y="4" width="16" height="16" fill="none" stroke="#e0731a" stroke-width="2.4"/><path d="M5 11l4 4 11-12" fill="none" stroke="#e0731a" stroke-width="3"/></svg>Videos are revealed at the right moment based on behavioral models that are built on the device. They appear as notifications, fullscreen videos, overlays or wallpapers. Works for both CorvoOS and NimbusOS.</li>
    <li style="height:130px"><svg width="22" height="22" viewBox="0 0 22 22"><rect x="1" y="4" width="16" height="16" fill="none" stroke="#e0731a" stroke-width="2.4"/><path d="M5 11l4 4 11-12" fill="none" stroke="#e0731a" stroke-width="3"/></svg>The initial target customers are low-cost MVNOs, like Skylark Mobile and Pinwheel Wireless here in the US, and low-ARPU carriers in APAC, like Orbis Telecom in the Philippines</li>
    <li style="height:130px"><svg width="22" height="22" viewBox="0 0 22 22"><rect x="1" y="4" width="16" height="16" fill="none" stroke="#e0731a" stroke-width="2.4"/><path d="M5 11l4 4 11-12" fill="none" stroke="#e0731a" stroke-width="3"/></svg>The message resonates with customers like Orbis. They have 55 million subs and their ARPU is $3.50 and falling. If we can turn those $3.50 customers into a $4.00 customer, that's very meaningful for them</li>
    <li style="height:130px"><svg width="22" height="22" viewBox="0 0 22 22"><rect x="1" y="4" width="16" height="16" fill="none" stroke="#e0731a" stroke-width="2.4"/><path d="M5 11l4 4 11-12" fill="none" stroke="#e0731a" stroke-width="3"/></svg>Orbis also has a young and video-centric subscriber base, which is extremely price sensitive. They have a number of different properties that we can work with.</li>
    <li><svg width="22" height="22" viewBox="0 0 22 22"><rect x="1" y="4" width="16" height="16" fill="none" stroke="#e0731a" stroke-width="2.4"/><path d="M5 11l4 4 11-12" fill="none" stroke="#e0731a" stroke-width="3"/></svg>In terms of traction, we just went live with Skylark Mobile now here in the US. The early metrics are encouraging, with a CPM of around $6, but we can see that getting to $10 by time we've finished optimizing the UX and the analytics. Every handset sold is preloaded with our library. The user doesn't have to download or opt-in to anything.</li>
  </ul>
  <a class="btn btn-view abs">View All</a>
</section>

<section class="team abs">
  <h2 class="section-title abs" style="top:42px">Our Team</h2>
  <div class="slider-arrow abs" style="left:20px;top:264px"><svg width="12" height="16" viewBox="0 0 12 16"><path d="M9 2L3 8l6 6" fill="none" stroke="#777" stroke-width="2"/></svg></div>
  <div class="slider-arrow abs" style="left:1142px;top:264px"><svg width="12" height="16" viewBox="0 0 12 16"><path d="M3 2l6 6-6 6" fill="none" stroke="#777" stroke-width="2"/></svg></div>

  <blockquote class="quote dark abs" style="left:101px;top:156px">Lorem ipsum dolor sit amet, onsectietuer icing eliterei sed diam nonummy nibh euismod erere tincideuntr ut laoreet dolore gna werwerweere roererere aliquama aerere era</blockquote>
  <svg class="portrait abs" style="left:152px;top:378px" viewBox="0 0 160 112" role="img" aria-label="Portrait of Marcus, CEO"><polygon points="30,0 160,0 130,112 0,112" fill="#fff"/><polygon points="36,6 152,6 125,106 8,106" fill="#8a8f94"/></svg>
  <div class="abs" style="left:330px;top:412px"><div class="member-name">Marcus</div><div class="member-role">CEO, Velmora Media</div></div>

  <blockquote class="quote orange abs" style="left:619px;top:204px">Lorem ipsum dolor sit amet, onsectietuer icing eliterei sed diam nonummy nibh euismod erere tincideuntr ut laoreet dolore gna werwerweere roererere aliquama aerere era</blockquote>
  <svg class="portrait abs" style="left:636px;top:420px" viewBox="0 0 160 112" role="img" aria-label="Portrait of Glen, Vice President"><polygon points="30,0 160,0 130,112 0,112" fill="#fff"/><polygon points="36,6 152,6 125,106 8,106" fill="#7d8288"/></svg>
  <div class="abs" style="left:810px;top:458px"><div class="member-name">Glen</div><div class="member-role">Vice President, Velmora Media</div></div>
</section>

<section class="clients">
  <h2 class="section-title abs" style="top:2243px">Our Clients</h2>
  <svg class="client-arrow abs" style="left:36px" width="16" height="40" viewBox="0 0 16 40"><path d="M12 4L4 20l8 16" fill="none" stroke="#ccc" stroke-width="2"/></svg>
  <svg class="client-arrow abs" style="left:1146px" width="16" height="40" viewBox="0 0 16 40"><path d="M4 4l8 16-8 16" fill="none" stroke="#ccc" stroke-width="2"/></svg>
  <div class="client-box abs" style="left:81px;width:227px"><i></i>Halden TV</div>
  <div class="client-box abs" style="left:326px;width:180px">Streamwell</div>
  <div class="client-box abs" style="left:524px;width:180px">Ironbay</div>
  <div class="client-box abs" style="left:720px;width:162px"><i></i>Halden TV</div>
  <div class="client-box abs" style="left:900px;width:216px;font-size:17px">Larkspur Music Group</div>
</section>

<section class="partner abs">
  <div class="partner-badge abs"></div>
  <p class="partner-text abs"><strong>Contact Us</strong> For Details Of How To Become A Certified Developer Partner.</p>
</section>

<section class="download abs" role="img" aria-label="Photo of hands holding a smartphone">
  <h2 class="download-title abs">Fill Up The Form To Get Link For Downloading Sample Apps</h2>
  <a class="store-btn abs" style="left:405px"><span class="mark"></span>Download on the<b>App Market</b></a>
  <a class="store-btn abs" style="left:603px"><span class="mark"></span>GET IT ON<b>Play Shelf</b></a>
</section>

<section class="contact abs">
  <div class="mail-badge abs"><svg width="46" height="32" viewBox="0 0 46 32"><rect x="1" y="1" width="44" height="30" fill="none" stroke="#fff" stroke-width="2.5"/><path d="M1 1l22 18L45 1" fill="none" stroke="#fff" stroke-width="2.5"/></svg></div>
  <div class="field abs" style="left:102px;top:80px;width:486px;height:70px">Your Name</div>
  <div class="field abs" style="left:612px;top:80px;width:486px;height:70px">Your Email</div>
  <div class="field abs" style="left:102px;top:160px;width:996px;height:70px">Subject</div>
  <div class="field message abs" style="left:102px;top:240px;width:996px;height:142px">Message</div>
  <a class="btn btn-submit abs">Submit</a>
</section>

<footer class="site-footer abs">
  <p class="copyright abs">Copyright © 2016 Velmora Media. All Rights Reserved.</p>
  <div class="social abs"><span></span><span></span><span></span><span></span></div>
</footer>

</body>
</html>
```